Veltrane Group Business Card Design

The CEO is looking for a new trendy look for his business card.
You can stay with current branding or come up with something new/creative. It can be 3D, including Medical Office buildings. You can use our logo in a variety of colors. Please include name, title, company name, company website, email address, cell number

Target Market(s)

Real Estate Development and Construction

Industry/Entity Type

Health care real estate

Contact Information for Business Card

Rohesh Kamdar, CEO M-604.781.2249 E-roheshkamdar@veltrane.com Address:4180 Lindqvist Ave, Tampa, FL 33482 www.veltrane.com

Font styles to use
Other font styles liked:
• Be creative

Requirements
Must have
• Creative, trendy look
Nice to have
• Please go to our website to get a feel- www. veltrane.com
Should not have
• small fonts

```html
<!DOCTYPE html>
<html lang="en">
<head>
<meta charset="utf-8">
<title>Veltrane Group – Business Card</title>
<link rel="stylesheet" href="https://fonts.googleapis.com/css2?family=Montserrat:wght@300;400;700;800&display=swap">
<style>
  :root {
    --backdrop: #e6e6e6;
    --card-black: #111111;
    --pattern-dark: #1c1c1c;
    --pattern-mid: #4a4a4a;
    --pattern-light: #8a8a8a;
    --brand-red: #b61f2b;
    --brand-navy: #1b2d52;
    --text-grey: #555555;
    --card-white: #ffffff;
  }
  * { box-sizing: border-box; margin: 0; padding: 0; }
  html, body { width: 1200px; height: 1129px; overflow: hidden; }
  body {
    background: var(--backdrop);
    font-family: "Montserrat", Arial, sans-serif;
    position: relative;
  }
  .card {
    position: absolute;
    left: 240px;
    width: 720px;
    height: 420px;
    box-shadow: 0 10px 30px rgba(0,0,0,0.18);
  }
  .card-back {
    top: 60px;
    background: var(--card-black);
    padding: 26px;
  }
  .monogram-field {
    width: 100%;
    height: 100%;
    background: linear-gradient(135deg, var(--pattern-light) 0%, var(--pattern-mid) 35%, var(--pattern-dark) 75%, #0b0b0b 100%);
    opacity: 0.85;
  }
  .card-front {
    top: 640px;
    background: var(--card-white);
    padding: 40px 52px;
  }
  .company-name {
    font-weight: 800;
    font-size: 52px;
    line-height: 60px;
    color: var(--brand-red);
    letter-spacing: -1px;
  }
  .person-name {
    margin-top: 24px;
    font-weight: 700;
    font-size: 30px;
    line-height: 36px;
    color: var(--brand-red);
    text-transform: uppercase;
    letter-spacing: 1px;
  }
  .person-title {
    font-weight: 700;
    font-size: 22px;
    line-height: 28px;
    color: var(--brand-navy);
  }
  .address {
    margin-top: 14px;
    font-weight: 300;
    font-size: 20px;
    line-height: 26px;
    color: var(--text-grey);
    font-style: normal;
  }
  .contact-list { list-style: none; }
  .contact-item {
    display: flex;
    align-items: center;
    gap: 10px;
    font-weight: 300;
    font-size: 20px;
    line-height: 26px;
    color: var(--text-grey);
  }
  .contact-icon { width: 16px; height: 16px; flex: none; }
</style>
</head>
<body>
  <section class="card card-back">
    <div class="monogram-field" role="img" aria-label="Repeating glossy brand monogram pattern fading from silver to black, one monogram highlighted in red"></div>
  </section>

  <section class="card card-front">
    <div class="company-name">Veltrane Group</div>
    <div class="person-name">Rohesh Kamdar</div>
    <div class="person-title">CEO</div>
    <address class="address">4180 Lindqvist Ave,<br>Tampa, FL 33482</address>
    <ul class="contact-list">
      <li class="contact-item">
        <svg class="contact-icon" viewBox="0 0 16 16" aria-hidden="true"><rect x="4" y="1" width="8" height="14" rx="1.5" fill="none" stroke="#b61f2b" stroke-width="1.8"/><circle cx="8" cy="12.2" r="0.9" fill="#b61f2b"/></svg>
        604.781.2249
      </li>
      <li class="contact-item">
        <svg class="contact-icon" viewBox="0 0 16 16" aria-hidden="true"><rect x="1" y="3" width="14" height="10" rx="1" fill="#b61f2b"/><path d="M1.5 3.5 L8 9 L14.5 3.5" fill="none" stroke="#fff" stroke-width="1.3"/></svg>
        roheshkamdar@veltrane.com
      </li>
      <li class="contact-item">
        <svg class="contact-icon" viewBox="0 0 16 16" aria-hidden="true"><circle cx="8" cy="8" r="7" fill="#b61f2b"/><path d="M1 8 H15 M8 1 C5 4 5 12 8 15 M8 1 C11 4 11 12 8 15" fill="none" stroke="#fff" stroke-width="1"/></svg>
        www.veltrane.com
      </li>
    </ul>
  </section>
</body>
</html>
```